Animal Eye Clinic needs a Business card

We are a new veterinary ophthalmology practice (Ridgeline Pet Vision Care) and we need a business card designed. We only see animal eyes - we are not a regular veterinary clinic. We already have a logo. We are looking for a professional, good looking business card to hand out to our clients. We are looking for something simple but professional and contemporary. Our logo is likely the only picture/graphic that needs to be on the card.
Updates

Contact Information for Business Card

Delia Vossman, BSc, DVM, MSc, DipACVO
Veterinary Ophthalmologist

Phone: 250.418.3927
Email: ridgelinepetvisioncare@mailbox-example.net
Website: ridgelinepetvisioncare-example.net
Address: 1874 Thornbury Rd
Kelowna, BC, V1X 4M9

Colors

Designer to choose colors to be used in the design.

Requirements
Must have
• Our logo (attached)

```html
<!DOCTYPE html>
<html lang="en">
<head>
<meta charset="utf-8">
<title>Ridgeline Pet Vision Care – Business Card</title>
<link rel="stylesheet" href="https://fonts.googleapis.com/css2?family=Roboto:wght@400;700&display=swap">
<style>
  :root {
    --teal: #0e99aa;
    --teal-deep: #0b8797;
    --grey-text: #555a5e;
    --grey-shape: #7b7d7f;
    --paper: #ffffff;
    --backdrop: #e9ecee;
  }
  * { box-sizing: border-box; margin: 0; padding: 0; }
  html, body {
    width: 1200px; height: 913px; overflow: hidden;
    background: var(--backdrop);
    font-family: "Roboto", Arial, sans-serif;
  }
  .sheet {
    position: relative; width: 1200px; height: 913px;
    display: flex; align-items: center; justify-content: center; gap: 40px;
  }
  .card {
    position: relative; width: 560px; height: 320px;
    border-radius: 20px; overflow: hidden;
    box-shadow: 0 6px 20px rgba(0,0,0,.12);
  }
  /* Front */
  .card-front { background: var(--teal); display: flex; align-items: center; justify-content: center; }
  .brand { display: flex; align-items: center; gap: 16px; color: var(--paper); }
  .brand-dot { width: 54px; height: 54px; border-radius: 50%; border: 4px solid var(--paper); flex: none; }
  .brand-name { font-weight: 700; font-size: 30px; line-height: 1.05; letter-spacing: -0.5px; text-transform: uppercase; }
  /* Back */
  .card-back { background: var(--paper); }
  .artwork {
    position: absolute; left: 0; bottom: 0; width: 215px; height: 280px;
    border-radius: 0 60% 0 0;
    background: linear-gradient(160deg, var(--teal) 0%, var(--teal-deep) 60%, var(--grey-shape) 100%);
  }
  .details {
    position: absolute; right: 26px; top: 24px; width: 300px; text-align: right; color: var(--grey-text);
  }
  .details-brand { color: var(--teal); font-weight: 700; font-size: 18px; text-transform: uppercase; letter-spacing: -0.3px; }
  .person { margin-top: 16px; }
  .person-name { color: var(--teal); font-weight: 700; font-size: 20px; text-transform: uppercase; }
  .person-creds { color: var(--teal); font-size: 13px; margin-top: 2px; }
  .person-role { font-size: 13px; margin-top: 2px; }
  .address { margin-top: 16px; font-size: 13px; line-height: 1.45; }
  .contact { margin-top: 10px; font-size: 12px; line-height: 1.65; }
  .contact-row { display: flex; align-items: center; justify-content: flex-end; gap: 6px; white-space: nowrap; }
  .contact-icon { width: 12px; height: 12px; flex: none; }
</style>
</head>
<body>
<main class="sheet">
  <section class="card card-front">
    <div class="brand">
      <span class="brand-dot"></span>
      <span class="brand-name">Ridgeline<br>Pet Vision Care</span>
    </div>
  </section>

  <section class="card card-back">
    <div class="artwork" role="img" aria-label="Large illustration of a horse, dog and cat in silhouette"></div>
    <div class="details">
      <p class="details-brand">Ridgeline Pet Vision Care</p>
      <div class="person">
        <p class="person-name">Delia Vossman</p>
        <p class="person-creds">BSc, DVM, MSc, DipACVO</p>
        <p class="person-role">Veterinary Ophthalmologist</p>
      </div>
      <p class="address">1874 Thornbury Rd<br>Kelowna, BC, V1X 4M9</p>
      <div class="contact">
        <p class="contact-row">250.418.3927
          <svg class="contact-icon" viewBox="0 0 12 12"><circle cx="6" cy="6" r="6" fill="var(--teal)"/><path d="M3.6 3.2c.4-.3.8-.2 1 .2l.5 1c.1.3 0 .5-.2.7l-.3.3c.3.7.9 1.3 1.6 1.6l.3-.3c.2-.2.4-.3.7-.2l1 .5c.4.2.5.6.2 1-.5.6-1.1.8-1.8.5C5 8 4 7 3.5 5.4c-.3-.8-.2-1.6.1-2.2z" fill="#fff"/></svg>
        </p>
        <p class="contact-row">ridgelinepetvisioncare@mailbox-example.net
          <svg class="contact-icon" viewBox="0 0 12 12"><circle cx="6" cy="6" r="6" fill="var(--teal)"/><rect x="3" y="4" width="6" height="4.2" fill="#fff"/><path d="M3 4l3 2.4L9 4" fill="none" stroke="var(--teal)" stroke-width=".8"/></svg>
        </p>
        <p class="contact-row">ridgelinepetvisioncare-example.net
          <svg class="contact-icon" viewBox="0 0 12 12"><circle cx="6" cy="6" r="6" fill="var(--teal)"/><circle cx="6" cy="6" r="3" fill="none" stroke="#fff" stroke-width=".9"/><path d="M3 6h6M6 3c-1.2 1.6-1.2 4.4 0 6M6 3c1.2 1.6 1.2 4.4 0 6" fill="none" stroke="#fff" stroke-width=".7"/></svg>
        </p>
      </div>
    </div>
  </section>
</main>
</body>
</html>
```